Wordpress Design For Financial Investment Company

//** NEW WIREFRAME ADDED TO HELP WITH LAYOUT ISSUES. PLEASE REFER TO WIREFRAME IN ATTACHED FILES. NO DESIGN WILL BE CONSIDERED IF IT DOES NOT FOLLOW THE WIREFRAME. **//
//** PLEASE READ THE ENTIRE BRIEF INCLUDING ALL UPDATES TO THE BRIEF. THE CLIENT IS VERY SPECIFIC ABOUT WHAT THEY WANT AND I'VE COVERED SEVERAL THINGS IN THE UPDATES. THERE IS ALSO A VIDEO UPDATE THAT HAS SOME VALUABLE INFORMATION IN IT FOR THIS CONTEST. **//
The client is an investment advisor who needs a new website designed. The current site is http://www.velmorhold.example.
The client wants the site to be green to match the attached logo.
The home page should have relevant images in the rotator. No people hugging! This is a financial investment site, not a family counseling site.
Also, the client wants 4 buttons on the home page to highlight the 4 main areas they focus on:
Investment Advice and Education
General Financial Planning
Retirement Planning
401K Planning
The top right area of the site needs to have their phone number, a call to action, and 2 buttons.
Their phone number is 303-418-7719
The call to action should say something like "Call for a free consultation!"
The buttons need to say:
Login To Your Brokavell Account
Login To Your Quillbrook Account
The final design should communicate professionalism, financial safety and growth.
Main navigation should be:
Home
About Us
Associates
Services
Contact
Mission Statement (Could also be "Our Mission")
This is a site that the client likes: http://www.pkwadvisoryfirm.example/
Updates
The designs should not have:
Newsletter content. A newsletter sign up is fine
Learning Center
Calculators
Stock prices/tickers
The design should have a contact form on the page.
I have talked to my client and have some updates. I did a video update because I thought it would be easier to show what I'm trying to get across.
Reason: I am going to be extending the contest a few more days. I'm still not getting quite what I want and very few people are even trying to follow the creative brief and the updates to it.
PLEASE read the entire brief and the updates. There is also a video I made that explains everything. I've also attached a wireframe.
Thanks!
Target Market(s)
People looking for a high-end financial investment company.
Industry/Entity Type
Investment
Requirements
Must have
- !!FOLLOW THE WIREFRAME FOR LAYOUT!!
!!THEIR LOGO!!
4 buttons to highlight their main practice areas
Phone number in the top right
"Free Consultation" call to action
2 Login buttons in the top right
A contact form on the page.
Should not have
- The designs should not have:
Learning Center
Calculators
Stock prices/tickers

```html
<!DOCTYPE html>
<html lang="en">
<head>
<meta charset="utf-8">
<title>Velmor Holdings</title>
<link href="https://fonts.googleapis.com/css2?family=Roboto+Condensed:wght@400;700&family=Arimo:wght@400&family=Open+Sans:wght@400;600&family=Libre+Baskerville:ital@1&display=swap" rel="stylesheet">
<style>
:root{
  --teal:#3f6b65;
  --teal-dark:#335a55;
  --teal-light:#4b7a73;
  --copper:#9a5a3c;
  --brown:#7a3f26;
  --ink:#1c1c1c;
  --body:#333;
  --white:#fff;
  --rule:#ddd;
}
*{box-sizing:border-box;margin:0;padding:0}
html,body{width:935px;height:1200px;overflow:hidden;background:var(--white)}
body{position:relative;font-family:"Arimo",Arial,sans-serif;color:var(--body)}
.abs{position:absolute}
.head{font-family:"Roboto Condensed",sans-serif;font-weight:700;text-transform:uppercase}

/* header */
.site-header{left:0;top:0;width:935px;height:163px;background:var(--teal)}
.nav-band{left:0;top:36px;width:935px;height:66px;background:linear-gradient(180deg,#4f7f78,#416f69)}
.copper-line{left:0;width:935px;height:3px;background:var(--copper)}
.login-btn{top:4px;height:25px;border:1px solid #7aa39c;background:var(--teal-light);color:var(--white);font-size:8px;line-height:23px;text-align:center;white-space:nowrap}
.nav-item{top:47px;height:45px;line-height:45px;color:var(--white);font-size:11.5px;text-align:center;white-space:nowrap}
.nav-item.active{background:var(--teal-dark)}
.brand-seal{left:408px;top:8px;width:124px;height:124px;border-radius:50%;background:#c9b2a7;border:5px solid #3a2a24;display:flex;align-items:center;justify-content:center;text-align:center}
.brand-name{font-family:"Roboto Condensed",sans-serif;font-weight:700;color:#2a1d18;font-size:17px;line-height:19px}
.motto{left:322px;top:132px;width:291px;height:26px;background:var(--white);font-family:"Libre Baskerville",serif;font-style:italic;font-size:7px;line-height:26px;text-align:center;color:#222;clip-path:polygon(0 0,100% 0,96% 50%,100% 100%,0 100%,4% 50%)}
.cta-label{left:643px;top:114px;width:200px;color:var(--white);font-size:10px;text-align:right;white-space:nowrap}
.cta-phone{left:660px;top:128px;width:181px;color:var(--white);font-size:23px;text-align:right;font-weight:700;font-family:"Roboto Condensed",sans-serif;white-space:nowrap}

/* hero */
.hero{left:0;top:163px;width:935px;height:383px;background:linear-gradient(90deg,#b9c6c2 0%,#e6d7c2 30%,#efe7d9 55%,#f4f1ea 100%)}
.hero-title{left:517px;top:341px;color:var(--ink);font-size:22px;white-space:nowrap}
.hero-sub{left:518px;top:392px;width:330px;color:var(--ink);font-size:9.6px;line-height:14px}
.dot{top:525px;width:10px;height:10px;border-radius:50%;border:2px solid #777;background:#eee}
.dot-line{left:406px;top:530px;width:124px;height:1px;background:#888}

/* focus buttons */
.focus-btn{left:94px;width:202px;height:53px;background:var(--teal);color:var(--white);display:flex;align-items:center;padding-left:37px;font-size:11.5px;line-height:15px}
.focus-btn.current{background:var(--brown)}
.focus-btn svg{position:absolute;left:9px;top:50%;margin-top:-10px}

/* welcome */
.section-title{color:var(--teal);font-size:17px}
.welcome-rule{left:312px;top:594px;width:531px;height:1px;background:var(--rule)}
.welcome-photo{left:311px;top:610px;width:203px;height:198px;background:linear-gradient(135deg,#a7a27c,#e9d7bf 50%,#cfc6a3)}
.copy{font-size:8.8px;line-height:14px;text-align:justify;color:var(--body)}
.copy p+p{margin-top:14px}

.col-rule{height:2px;background:var(--teal)}
.thin-rule{height:1px;background:var(--rule)}
.more-btn{top:1025px;width:54px;height:21px;background:var(--teal);color:var(--white);font-size:10px;line-height:21px;text-align:center}

/* quick contact */
.quick-contact{left:608px;top:831px;width:234px;height:215px;background:var(--teal)}
.quick-contact .bar{position:absolute;left:0;top:34px;width:234px;height:1px;background:#5f8a83}
.field{left:619px;width:212px;background:var(--white);border-radius:5px;font-size:8.5px;color:#999;padding:6px 7px}
.submit{left:762px;top:1012px;width:69px;height:25px;border-radius:5px;background:linear-gradient(#f2f2f2,#c9c9c9);color:#888;font-size:12px;line-height:25px;text-align:center}

/* footer */
.site-footer{left:0;top:1066px;width:935px;height:134px;background:var(--teal);font-family:"Open Sans",sans-serif;color:var(--white)}
.newsletter{left:94px;top:1086px;width:193px;height:86px;background:#f3f3f3;border:3px solid #c8c8c8}
.newsletter .title{position:absolute;left:12px;top:9px;font-size:11.5px;color:#666;font-weight:600}
.newsletter .email{position:absolute;left:13px;top:29px;width:167px;height:21px;background:var(--white);border:1px solid #bbb;font-size:8px;color:#888;line-height:19px;padding-left:8px}
.newsletter .signup{position:absolute;left:133px;top:57px;width:47px;height:19px;border-radius:4px;background:#1c8fd3;color:var(--white);font-size:8px;line-height:19px;text-align:center;font-weight:600}
.foot-head{font-size:9.5px;font-weight:600}
.foot-list{font-size:9px;line-height:14.5px}
.social{top:1110px;width:24px;height:24px;border-radius:50%;background:#e9eef0;border:2px solid #cfd8da}
</style>
</head>
<body>

<header class="site-header abs"></header>
<div class="nav-band abs"></div>
<div class="copper-line abs" style="top:35px"></div>
<div class="copper-line abs" style="top:42px"></div>
<div class="copper-line abs" style="top:96px"></div>
<div class="copper-line abs" style="top:102px"></div>

<div class="login-btn head abs" style="left:579px;width:129px">Login to Brokavell Account</div>
<div class="login-btn head abs" style="left:713px;width:129px">Login to Quillbrook Account</div>

<nav>
  <div class="nav-item head abs active" style="left:94px;width:54px">Home</div>
  <div class="nav-item head abs" style="left:190px;width:74px">About Us</div>
  <div class="nav-item head abs" style="left:300px;width:84px">Associates</div>
  <div class="nav-item head abs" style="left:545px;width:100px">Services</div>
  <div class="nav-item head abs" style="left:668px;width:88px">Our Mission</div>
  <div class="nav-item head abs" style="left:776px;width:62px">Contact</div>
</nav>

<div class="brand-seal abs"><span class="brand-name">VELMOR<br>HOLDINGS</span></div>
<div class="motto abs">“Always do right. This will gratify some people &amp; astonish the rest.”</div>
<div class="cta-label head abs">Call for a free consultation:</div>
<div class="cta-phone abs">303-418-7719</div>

<section class="hero abs" role="img" aria-label="Photo of a smiling retired couple outdoors with a soft blurred background"></section>
<h1 class="hero-title head abs">Retirement &amp; Education Plans</h1>
<p class="hero-sub head abs">Sed ut perspiciatis unde omnis iste natus error sit voluptatem accusantium doloremque laudantium</p>
<div class="dot-line abs"></div>
<div class="dot abs" style="left:401px;background:#fff;border-color:#ddd"></div>
<div class="dot abs" style="left:432px"></div>
<div class="dot abs" style="left:463px"></div>
<div class="dot abs" style="left:494px"></div>
<div class="dot abs" style="left:525px"></div>

<svg width="0" height="0" style="position:absolute"><defs>
<g id="chev"><circle cx="10" cy="10" r="10" fill="#fff" fill-opacity=".2"/><path d="M8 5l5 5-5 5" stroke="#fff" stroke-opacity=".6" stroke-width="2.4" fill="none"/></g></defs></svg>

<a class="focus-btn current head abs" style="top:570px"><svg width="20" height="20"><use href="#chev"/></svg>Investment Advice<br>and Education</a>
<a class="focus-btn head abs" style="top:630px"><svg width="20" height="20"><use href="#chev"/></svg>General Financial Planning</a>
<a class="focus-btn head abs" style="top:692px"><svg width="20" height="20"><use href="#chev"/></svg>Retirement Planning</a>
<a class="focus-btn head abs" style="top:754px"><svg width="20" height="20"><use href="#chev"/></svg>401K Planning</a>

<h2 class="section-title head abs" style="left:312px;top:564px">Welcome!</h2>
<div class="welcome-rule abs"></div>
<div class="welcome-photo abs" role="img" aria-label="Photo of a happy family of three embracing on a sofa"></div>
<div class="copy abs" style="left:526px;top:610px;width:317px">
  <p>Sed ut perspiciatis unde omnis iste natus error sit voluptatem accusantium doloremque laudantium, totam rem aperiam, eaque ipsa quae ab illo inventore veritatis et quasi architecto beatae vitae dicta sunt explicabo.</p>
  <p>Nemo enim ipsam voluptatem quia voluptas sit aspernatur aut odit aut fugit, sed quia consequuntur magni dolores eos qui ratione voluptatem sequi nesciunt. Neque porro quisquam est, qui dolorem ipsum quia dolor sit amet, consectetur, adipisci velit, sed quia non numquam eius modi tempora incidunt ut labore et dolore magnam aliquam quaerat voluptatem.</p>
  <p>Ut enim ad minima veniam, quis nostrum exercitationem ullam corporis suscipit laboriosam, nisi ut aliquid ex ea commodi consequatur? Quis autem vel eum iure reprehenderit qui in ea voluptate velit esse quam nihil molestiae consequatur, vel illum qui dolorem eum fugiat quo voluptas nulla pariatur</p>
</div>

<h2 class="section-title head abs" style="left:94px;top:834px">Our Services</h2>
<div class="col-rule abs" style="left:94px;top:861px;width:233px"></div>
<div class="copy abs" style="left:94px;top:877px;width:235px">
  <p>perspiciatis unde omnis iste natus error sit voluptatem accusantium doloremque laudantium, totam rem aperiam, eaque ipsa quae ab illo inventore veritatis et quasi architecto beatae vitae dicta sunt explicabo.</p>
  <p>Nemo enim ipsam voluptatem quia voluptas sit aspernatur aut odit aut fugit, sed quia consequuntur magniqui dolorem ipsum quia dolor sit amet, consectetur, adipisci velit, sed quia non numquam eius modi tempora incidunt</p>
</div>
<div class="thin-rule abs" style="left:94px;top:1013px;width:235px"></div>
<div class="more-btn head abs" style="left:94px">More</div>

<h2 class="section-title head abs" style="left:351px;top:834px">Our Firm</h2>
<div class="col-rule abs" style="left:351px;top:861px;width:234px"></div>
<div class="copy abs" style="left:351px;top:877px;width:235px">
  <p>perspiciatis unde omnis iste natus error sit voluptatem accusantium doloremque laudantium, totam rem aperiam, eaque ipsa quae ab illo inventore veritatis et quasi architecto beatae vitae dicta sunt explicabo.</p>
  <p>Nemo enim ipsam voluptatem quia voluptas sit aspernatur aut odit aut fugit, sed quia consequuntur magniqui dolorem ipsum quia dolor sit amet, consectetur, adipisci velit, sed quia non numquam eius modi tempora incidunt</p>
</div>
<div class="thin-rule abs" style="left:351px;top:1013px;width:235px"></div>
<div class="more-btn head abs" style="left:351px">More</div>

<aside class="quick-contact abs"><div class="bar"></div></aside>
<h2 class="head abs" style="left:623px;top:838px;color:#fff;font-size:16px">Quick Contact</h2>
<div class="field abs" style="top:877px;height:25px">Name</div>
<div class="field abs" style="top:914px;height:25px">Email</div>
<div class="field abs" style="top:950px;height:50px">Comments</div>
<div class="submit head abs">Submit</div>

<footer class="site-footer abs"></footer>
<div class="newsletter abs">
  <div class="title">Join Our Newsletter</div>
  <div class="email">Enter Your Email Address</div>
  <div class="signup">Sign Up</div>
</div>

<div class="abs" style="left:332px;top:1084px;font-family:'Open Sans',sans-serif;color:#fff">
  <div class="foot-head">Company</div>
  <div class="foot-list" style="margin-top:10px;line-height:18px">Privacy<br>Terms Of Use<br>Terms Of Trade<br>PO T&amp;C's</div>
</div>
<div class="abs" style="left:470px;top:1084px;font-family:'Open Sans',sans-serif;color:#fff">
  <div class="foot-head">Contact Us</div>
  <div class="foot-list" style="margin-top:10px">Suite 9, 214 Harlow Lane<br>Brenford Vic 3120<br>T:&nbsp;&nbsp;&nbsp;&nbsp;&nbsp;+61 3 5527 4408<br>F:&nbsp;&nbsp;&nbsp;&nbsp;&nbsp;+61 3 5527 4490<br>E:&nbsp;&nbsp;&nbsp;&nbsp;&nbsp;info@velmorhold.example</div>
</div>
<div class="abs" style="left:654px;top:1084px;font-family:'Open Sans',sans-serif;color:#fff">
  <div class="foot-head">Follow Us Online</div>
</div>
<div class="social abs" style="left:655px"></div>
<div class="social abs" style="left:683px"></div>
<div class="social abs" style="left:711px"></div>
<div class="social abs" style="left:739px"></div>
<div class="foot-list abs" style="left:656px;top:1148px;font-family:'Open Sans',sans-serif;color:#fff;line-height:16px">Privacy Policy | Terms of Services | Sitemap<br>Copyright © 2013. All Rights Reserved.</div>

</body>
</html>
```